Volbrey Inc Business Card

Looking to get an updated business card for a Contract Machining company (www.volbreyinc.example) - looking for a clean design the portrays the technical nature of the business - colors can follow the website design and be in any combination that makes sense (red black, white, metallic or silver) - logos attached for use also. Would like space for: Name, title, business phone (555 214-3086), cell phone , website (www.volbreyinc.example) - possibly QR code could be integrated for website (designer choice), business address - 418 Harlow Bend, Brennick Falls, BF 48199 (cards will be for 4 employees, I will either need to modify a template or I can provide individual information)
Target Market(s)
Aerospace, defense and medical device manufacturing companies that need machining
Industry/Entity Type
Machining for aerospace, defense, medical
Contact Information for Business Card
Name, Title, Business Phone, Cell Phone, email, business website and business address
Look and feel

```html
<!DOCTYPE html>
<html lang="en">
<head>
<meta charset="UTF-8">
<title>Volbrey Inc Business Card</title>
<link href="https://fonts.googleapis.com/css2?family=Roboto:wght@400;500;700&display=swap" rel="stylesheet">
<style>
  :root {
    --stage: #3a3a3a;
    --brand-red: #b01e24;
    --paper: #ffffff;
    --ink: #3b3b3b;
    --muted: #7a7a7a;
    --rule: #c9c9c9;
    --band-grey: #6e6e6e;
    --ghost: #f7ecec;
  }
  * { box-sizing: border-box; margin: 0; padding: 0; }
  html, body { width: 1200px; height: 689px; overflow: hidden; }
  body {
    background: var(--stage);
    font-family: "Roboto", Arial, sans-serif;
    position: relative;
  }
  .card {
    position: absolute;
    top: 200px;
    width: 500px;
    height: 286px;
    border-radius: 16px;
    overflow: hidden;
  }
  /* Back of card */
  .card-back { left: 60px; background: var(--brand-red); }
  .back-badge {
    position: absolute; left: 165px; top: 48px;
    width: 170px; height: 170px; border-radius: 50%;
    background: var(--paper);
    display: flex; align-items: center; justify-content: center;
  }
  .back-badge .brand-name {
    color: var(--brand-red); font-weight: 700; font-size: 19px; letter-spacing: 1px;
    white-space: nowrap;
  }
  .back-url {
    position: absolute; left: 0; right: 0; top: 240px;
    text-align: center; color: var(--paper); font-size: 13px; letter-spacing: .3px;
  }
  /* Front of card */
  .card-front { left: 640px; background: var(--paper); }
  .ghost-ring {
    position: absolute; left: 20px; top: 80px;
    width: 240px; height: 240px; border-radius: 50%;
    border: 22px solid var(--ghost);
  }
  .brand-block {
    position: absolute; right: 34px; top: 24px;
    display: flex; flex-direction: column; align-items: center;
  }
  .brand-dot {
    width: 74px; height: 74px; border-radius: 50%; background: var(--brand-red);
  }
  .brand-block .brand-name {
    margin-top: 8px; color: var(--brand-red); font-weight: 700; font-size: 20px; letter-spacing: 1px;
    white-space: nowrap;
  }
  .divider {
    position: absolute; left: 34px; right: 34px; top: 140px;
    border-top: 1px solid var(--rule);
  }
  .address {
    position: absolute; right: 34px; top: 152px;
    text-align: right; color: var(--ink); font-size: 12px; line-height: 16px; font-style: normal;
  }
  .person { position: absolute; left: 34px; top: 162px; }
  .person-name { color: var(--brand-red); font-weight: 700; font-size: 19px; line-height: 24px; }
  .person-title {
    color: var(--muted); font-size: 11px; padding-bottom: 6px;
    border-bottom: 1px solid var(--rule); width: 150px; margin-bottom: 6px;
  }
  .contact-list { list-style: none; }
  .contact-list li {
    display: flex; align-items: center; gap: 7px;
    color: var(--ink); font-size: 12px; line-height: 17px; white-space: nowrap;
  }
  .contact-list svg { width: 10px; height: 10px; fill: var(--brand-red); flex: none; }
  .band-grey { position: absolute; left: 0; right: 0; bottom: 12px; height: 3px; background: var(--band-grey); }
  .band-red { position: absolute; left: 0; right: 0; bottom: 0; height: 10px; background: var(--brand-red); }
</style>
</head>
<body>
  <section class="card card-back">
    <div class="back-badge"><span class="brand-name">VOLBREY INC.</span></div>
    <p class="back-url">www.volbreyinc.example</p>
  </section>

  <section class="card card-front">
    <div class="ghost-ring"></div>
    <div class="brand-block">
      <div class="brand-dot"></div>
      <span class="brand-name">VOLBREY INC.</span>
    </div>
    <div class="divider"></div>
    <address class="address">
      418 Harlow Bend<br>
      Brennick Falls, BF 48199<br>
      www.volbreyinc.example
    </address>
    <div class="person">
      <p class="person-name">Dana Whitlow</p>
      <p class="person-title">President</p>
      <ul class="contact-list">
        <li><svg viewBox="0 0 10 10"><path d="M2 0.5 L3.8 2.6 L2.9 3.7 Q4 6 6.3 7.1 L7.4 6.2 L9.5 8 L8.3 9.5 Q4.5 9.5 2 7 Q0.5 4.5 0.5 1.7 Z"/></svg>555 214-3086</li>
        <li><svg viewBox="0 0 10 10"><path d="M2.5 0 H7.5 V10 H2.5 Z M3.4 1 V8 H6.6 V1 Z"/></svg>555 630-4471</li>
        <li><svg viewBox="0 0 10 10"><path d="M0 2 H10 V8.5 H0 Z M0.8 2.6 L5 5.6 L9.2 2.6"/></svg>info@volbreyinc.example</li>
      </ul>
    </div>
    <div class="band-grey"></div>
    <div class="band-red"></div>
  </section>
</body>
</html>
```